Website for Dental Office - The Bright Arch Clinic

The bright arch clinic is a dental office offering cosmetic dentistry, general dentistry, and multi-specialty dental care all under one roof in our state-of-the-art cosmetic dental center. We are particularly striving to provide services that fit the need of the young generation. Thus, we hope to have a modern, professional concise website that represents our spirit.

*Should be able to switch from English to Chinese

6 sections besides homepage:
Home, Meet us, Services,
Patient Info, Cases&Reviews, Blog, Contact

The Services sections should contain multiple subsections such as cleaning and prevention, cosmetic dentistry, implant dentistry, removable dentures, etc...
The Patient Info section is also intended to contain several subsections such as
New Patient offer, accepted Insurance, patient portal, helpful tips, etc...

Target Market(s)

young generation

Coding

Coded - Design and coding required

Number of Pages Required

5+ page

Font styles to use
Sans Serif

Colors
0592cd
33a6d7
85cae6
00a990
33b8a4
86cfc6
cee9f5
cfeae6
3277b5

Requirements
Must have
• *Should be able to switch from English to Chinese
Nice to have
• http://www.thebrightarchclinic.com/
• As a reference, the above link is the current website, but we would like to change the appearance and the content (our new logo's picture is attached)

```html
<!DOCTYPE html>
<html lang="en">
<head>
<meta charset="utf-8">
<title>The Bright Arch Clinic</title>
<link href="https://fonts.googleapis.com/css2?family=Poppins:wght@400;500;600;700;800&family=Open+Sans:wght@400;600;700&display=swap" rel="stylesheet">
<style>
:root{
  --blue:#0592cd;
  --blue-mid:#33a6d7;
  --blue-light:#85cae6;
  --blue-pale:#cee9f5;
  --teal:#00a990;
  --teal-mid:#33b8a4;
  --teal-light:#86cfc6;
  --teal-pale:#cfeae6;
  --navy:#3277b5;
  --ink:#222;
  --text:#555;
  --white:#fff;
  --footer:#111;
}
*{box-sizing:border-box;margin:0;padding:0}
html,body{width:1200px;height:4456px;overflow:hidden;background:var(--white)}
body{position:relative;font-family:"Open Sans",Arial,sans-serif;color:var(--text)}
h2.section-title{position:absolute;left:0;width:1200px;text-align:center;font-family:"Poppins",sans-serif;font-weight:700;font-size:40px;letter-spacing:2px;color:var(--ink)}
.title-arc{position:absolute;left:570px;width:60px;height:14px}

/* header */
.site-header{position:absolute;top:0;left:0;width:1200px;height:112px;background:var(--white);z-index:3}
.brand{position:absolute;display:flex;align-items:center;gap:12px;font-family:"Poppins",sans-serif;font-weight:700;color:var(--blue)}
.brand-square{width:30px;height:30px;background:var(--blue);border-radius:4px;flex:none}
.site-header .brand{left:144px;top:24px;font-size:24px}
.main-nav{position:absolute;left:380px;top:76px;display:flex;gap:30px;font-family:"Poppins",sans-serif;font-weight:600;font-size:17px;color:#333}
.main-nav .active{color:var(--blue);border-bottom:3px solid var(--blue);padding-bottom:4px}
.toll{position:absolute;left:800px;top:14px;font-family:"Poppins",sans-serif}
.toll small{display:block;font-size:13px;color:#666}
.toll strong{font-size:26px;color:var(--navy)}
.lang{position:absolute;left:996px;top:22px;width:96px;height:34px;border:1px solid #ccc;border-radius:4px;font-size:14px;line-height:32px;padding-left:10px;color:#333}
.lang::after{content:"";position:absolute;right:10px;top:13px;border:5px solid transparent;border-top-color:#555}

/* hero */
.hero{position:absolute;top:112px;left:0;width:1200px;height:700px;background:linear-gradient(100deg,#dfe7e9 0%,#f1ede8 45%,#e8d9cc 100%)}
.hero-photo{position:absolute;left:540px;top:0;width:560px;height:680px;background:radial-gradient(ellipse at 50% 45%,#e6c2a8 0%,#d8b39a 35%,rgba(232,217,204,0) 70%)}
.hero h1{position:absolute;left:144px;top:228px;font-family:"Poppins",sans-serif;font-weight:800;font-size:68px;line-height:80px;color:#2a2a2a;letter-spacing:2px}
.btn{display:inline-block;font-family:"Poppins",sans-serif;font-weight:600;color:var(--white);text-transform:uppercase}
.hero .btn{position:absolute;left:144px;top:412px;background:var(--blue);font-size:16px;padding:12px 22px;border-radius:3px}
.slider-arrow{position:absolute;top:322px;width:40px;height:40px;border-radius:50%;background:#333}
.slider-arrow svg{position:absolute;left:12px;top:12px}
.hero-wave{position:absolute;left:0;top:640px;width:1200px;height:180px}

/* services */
.services-cards{position:absolute;left:144px;top:1020px;display:flex;gap:16px}
.service-card{width:220px;height:400px;border-radius:14px;color:var(--white);text-align:center;overflow:hidden;position:relative}
.service-card.blue{background:var(--blue)}
.service-card.teal{background:var(--teal)}
.service-card.navy{background:var(--navy)}
.service-photo{width:196px;height:210px;margin:12px auto 0;border-radius:98px 98px 8px 8px}
.service-card h3{font-family:"Poppins",sans-serif;font-size:17px;font-weight:700;margin:16px 0 8px}
.service-card p{font-size:12.5px;line-height:17px;padding:0 18px}
.read-more{display:inline-block;margin-top:14px;font-family:"Poppins",sans-serif;font-size:12px;font-weight:600;border-bottom:1px solid var(--white)}

/* welcome */
.welcome{position:absolute;top:1440px;left:0;width:1200px;height:760px;background:linear-gradient(100deg,var(--teal-mid) 0%,var(--blue-mid) 55%,var(--blue) 100%)}
.welcome-curves{position:absolute;left:0;width:1200px;height:160px}
.welcome-photo{position:absolute;left:160px;top:200px;width:380px;height:380px;border-radius:50%;border:10px solid var(--white);background:linear-gradient(135deg,#9fd6ee,#4aa7d4 60%,#2f7fb0)}
.welcome-copy{position:absolute;left:580px;top:218px;width:520px;color:var(--white)}
.welcome-copy .kicker{font-family:"Poppins",sans-serif;font-size:30px;font-weight:400}
.welcome-copy h2{font-family:"Poppins",sans-serif;font-size:40px;font-weight:700;margin-top:-2px}
.welcome-copy p{font-size:15px;line-height:27px;margin-top:14px}
.welcome-copy .btn{margin-top:22px;background:var(--white);color:var(--navy);font-size:15px;padding:10px 20px;border-radius:3px}

/* patient info */
.patient-cols{position:absolute;left:144px;top:2340px;display:flex;gap:20px}
.patient-col{width:225px;text-align:center}
.patient-icon{height:80px}
.patient-col h3{font-family:"Poppins",sans-serif;font-size:18px;font-weight:600;color:var(--ink);margin-top:20px}
.patient-col p{font-size:13px;line-height:19px;margin-top:10px;padding:0 8px}
.patient-col .chev{margin-top:14px}

/* blog */
.blog{position:absolute;top:2620px;left:0;width:1200px;height:840px;background:linear-gradient(100deg,var(--blue-mid) 0%,var(--blue) 60%,var(--navy) 100%)}
.blog-curves{position:absolute;left:0;width:1200px;height:150px}
.blog h2.section-title{color:var(--white);top:168px}
.blog-cards{position:absolute;left:144px;top:300px;display:flex;gap:16px}
.blog-card{width:296px;height:400px;background:var(--white);box-shadow:0 6px 16px rgba(0,0,0,.2)}
.blog-photo{width:276px;height:200px;margin:10px auto 0}
.blog-card h3{font-family:"Poppins",sans-serif;font-size:17px;font-weight:700;color:var(--ink);text-align:center;margin-top:26px}
.blog-card p{font-size:12.5px;line-height:18px;text-align:center;padding:0 22px;margin-top:10px}
.blog-date{display:flex;align-items:center;justify-content:center;gap:8px;margin-top:14px;font-size:13px;color:var(--blue)}

/* reviews */
.review-arrow{position:absolute;top:3706px;width:46px;height:46px;background:var(--blue-light);display:flex;align-items:center;justify-content:center}
.review-brand{position:absolute;left:170px;top:3640px;width:340px;height:240px;display:flex;align-items:center;justify-content:center;gap:14px;font-family:"Poppins",sans-serif;font-weight:700;font-size:30px;line-height:40px;color:var(--blue)}
.review-brand .brand-square{width:40px;height:40px}
.quote-mark{position:absolute;font-family:"Poppins",sans-serif;font-weight:800;font-size:90px;line-height:90px;color:var(--blue-light)}
.review-text{position:absolute;left:600px;top:3614px;width:440px;font-size:17px;line-height:29px;font-style:italic;color:#444}
.review-author{position:absolute;left:530px;top:3824px;font-size:16px;line-height:24px;color:#333}

/* footer */
.site-footer{position:absolute;top:3936px;left:0;width:1200px;height:444px;background:var(--footer);color:#ddd}
.site-footer .footer-brand{left:120px;top:72px;width:180px;flex-direction:column;gap:8px;text-align:center;font-size:16px;line-height:20px;color:var(--blue-mid)}
.footer-brand .brand-square{width:36px;height:36px;background:var(--blue-mid)}
.social{position:absolute;left:162px;top:150px;display:flex;gap:8px}
.social span{width:20px;height:20px;border:2px solid #ddd;border-radius:50%}
.footer-col{position:absolute;top:76px}
.footer-col h4{font-family:"Poppins",sans-serif;font-size:18px;font-weight:700;color:var(--white);margin-bottom:20px}
.footer-col p{font-size:13px;line-height:19px}
.email-field{margin-top:18px;width:272px;height:40px;background:var(--white);border-radius:3px;padding-left:14px;line-height:40px;font-size:13px;color:#888}
.subscribe{margin-top:22px;background:var(--teal);font-size:14px;padding:9px 20px;border-radius:18px}
.contact-line{display:flex;gap:14px;font-size:14px;line-height:20px;margin-bottom:18px}
.contact-line svg{flex:none;margin-top:2px}
.quick-links li{list-style:none;font-size:15px;line-height:30px}
.copyright{position:absolute;top:4380px;left:0;width:1200px;height:76px;background:#1a1a1a;color:#ccc;font-size:14px;text-align:center;line-height:76px}
</style>
</head>
<body>

<header class="site-header">
  <div class="brand"><span class="brand-square"></span>The Bright Arch Clinic</div>
  <nav class="main-nav">
    <span class="active">HOME</span><span>MEET US</span><span>SERVICES</span><span>PATIENT INFO</span><span>CASES &amp; REVIEWS</span><span>BLOG</span><span>CONTACT</span>
  </nav>
  <div class="toll"><small>Toll Free:</small><strong>617.555.0142</strong></div>
  <div class="lang">English</div>
</header>

<section class="hero">
  <div class="hero-photo" role="img" aria-label="Photo of a smiling young woman resting her chin on her hand"></div>
  <h1>YOUR SMILE.<br>OUR PASSION</h1>
  <span class="btn">Request an appointment</span>
  <span class="slider-arrow" style="left:52px"><svg width="16" height="16"><path d="M11 2 5 8l6 6" stroke="#fff" stroke-width="2.5" fill="none"/></svg></span>
  <span class="slider-arrow" style="left:1108px"><svg width="16" height="16"><path d="M5 2l6 6-6 6" stroke="#fff" stroke-width="2.5" fill="none"/></svg></span>
  <svg class="hero-wave" viewBox="0 0 1200 180" preserveAspectRatio="none">
    <path d="M0 60 Q600 200 1200 60 L1200 180 L0 180Z" fill="#fff"/>
    <path d="M0 64 Q600 204 1200 64" stroke="var(--blue)" stroke-width="6" fill="none"/>
  </svg>
</section>

<h2 class="section-title" style="top:906px">OUR SERVICES</h2>
<svg class="title-arc" style="top:966px" viewBox="0 0 60 14"><path d="M4 3 Q30 16 56 3" stroke="var(--blue)" stroke-width="4" fill="none" stroke-linecap="round"/></svg>

<div class="services-cards">
  <article class="service-card blue">
    <div class="service-photo" role="img" aria-label="Photo of a patient at a cleaning appointment" style="background:linear-gradient(160deg,#e9d5c5,#9ec9de)"></div>
    <h3>Cleaning &amp; Prevention</h3>
    <p>Regular cleanings and checkups keep teeth strong, gums healthy and small problems from growing.</p>
    <span class="read-more">READ MORE</span>
  </article>
  <article class="service-card teal">
    <div class="service-photo" role="img" aria-label="Photo of a dentist working on a smile" style="background:linear-gradient(160deg,#f2e3dc,#c97b78)"></div>
    <h3>Cosmetic Dentistry</h3>
    <p>Whitening, veneers and bonding shape a brighter smile that suits your face and your style.</p>
    <span class="read-more">READ MORE</span>
  </article>
  <article class="service-card navy">
    <div class="service-photo" role="img" aria-label="Photo of a dental implant model" style="background:linear-gradient(160deg,#f4f4f4,#b9c4cc)"></div>
    <h3>Implant Dentistry</h3>
    <p>Stable, natural looking implants replace missing teeth and restore a confident, easy bite.</p>
    <span class="read-more">READ MORE</span>
  </article>
  <article class="service-card blue">
    <div class="service-photo" role="img" aria-label="Photo of hands holding a denture" style="background:linear-gradient(160deg,#f6ebe6,#d99a94)"></div>
    <h3>Removable Dentures</h3>
    <p>Comfortable full and partial dentures are fitted with care to look and feel like your own.</p>
    <span class="read-more">READ MORE</span>
  </article>
</div>

<section class="welcome">
  <svg class="welcome-curves" style="top:0" viewBox="0 0 1200 160" preserveAspectRatio="none"><path d="M0 0H1200V40Q600 170 0 40Z" fill="#fff"/></svg>
  <svg class="welcome-curves" style="top:600px" viewBox="0 0 1200 160" preserveAspectRatio="none"><path d="M0 160H1200V100Q600 -10 0 100Z" fill="#fff"/></svg>
  <div class="welcome-photo" role="img" aria-label="Photo of a smiling boy in the dental chair"></div>
  <div class="welcome-copy">
    <div class="kicker">Welcome to</div>
    <h2>The Bright Arch Clinic</h2>
    <p>Welcome to The Bright Arch Clinic, where we specialize in General and Cosmetic Dentistry, Dental Implants, Periodontics (Gum Surgery), Endodontics (Root Canal Treatment) and Reconstructive Dentistry for patients in Brookline and all of the surrounding neighborhoods. Our friendly team makes every visit calm, clear and comfortable.</p>
    <span class="btn">Read more</span>
  </div>
</section>

<h2 class="section-title" style="top:2196px">PATIENT INFO</h2>
<svg class="title-arc" style="top:2256px" viewBox="0 0 60 14"><path d="M4 3 Q30 16 56 3" stroke="var(--blue)" stroke-width="4" fill="none" stroke-linecap="round"/></svg>

<div class="patient-cols">
  <div class="patient-col">
    <svg class="patient-icon" width="80" height="80" viewBox="0 0 80 80" fill="none" stroke="var(--teal)" stroke-width="3"><path d="M24 22c-8 0-12 8-10 18 2 12 6 28 12 28 5 0 5-14 14-14s9 14 14 14c6 0 10-16 12-28 2-10-2-18-10-18-6 0-10 4-16 4s-10-4-16-4z"/></svg>
    <h3>New Patient offer</h3>
    <p>Enjoy a welcome exam, cleaning and x-rays at a special rate on your first visit with us.</p>
    <svg class="chev" width="14" height="10"><path d="M2 2l5 5 5-5" stroke="#777" stroke-width="2" fill="none"/></svg>
  </div>
  <div class="patient-col">
    <svg class="patient-icon" width="80" height="80" viewBox="0 0 80 80" fill="none" stroke="var(--teal)" stroke-width="3"><rect x="18" y="12" width="44" height="58" rx="3"/><path d="M30 12v-4h20v4M28 32h24M28 44h24M28 56h14"/></svg>
    <h3>Accepted Insurance</h3>
    <p>We work with most major dental plans and help you understand your benefits before treatment.</p>
    <svg class="chev" width="14" height="10"><path d="M2 2l5 5 5-5" stroke="#777" stroke-width="2" fill="none"/></svg>
  </div>
  <div class="patient-col">
    <svg class="patient-icon" width="80" height="80" viewBox="0 0 80 80" fill="none" stroke="var(--teal)" stroke-width="3"><rect x="16" y="14" width="48" height="56" rx="3"/><path d="M16 28h48M30 44c0-6 4-8 10-8s10 2 10 8c0 8-4 14-10 14s-10-6-10-14z"/></svg>
    <h3>Patient Portal</h3>
    <p>Book visits, fill in forms and review your records online at any time from any device.</p>
    <svg class="chev" width="14" height="10"><path d="M2 2l5 5 5-5" stroke="#777" stroke-width="2" fill="none"/></svg>
  </div>
  <div class="patient-col">
    <svg class="patient-icon" width="80" height="80" viewBox="0 0 80 80" fill="none" stroke="var(--teal)" stroke-width="3"><path d="M28 18c-8 0-12 8-10 18 2 12 6 28 12 28 5 0 5-14 10-14s5 14 10 14c6 0 10-16 12-28 2-10-2-18-10-18-5 0-8 3-12 3s-7-3-12-3z"/><path d="M56 10l4 6M64 20l6-2"/></svg>
    <h3>Helpful Tips</h3>
    <p>Simple daily habits for brushing, flossing and eating well to keep your smile bright.</p>
    <svg class="chev" width="14" height="10"><path d="M2 2l5 5 5-5" stroke="#777" stroke-width="2" fill="none"/></svg>
  </div>
</div>

<section class="blog">
  <svg class="blog-curves" style="top:0" viewBox="0 0 1200 150" preserveAspectRatio="none"><path d="M0 0H1200V30Q600 160 0 30Z" fill="#fff"/></svg>
  <svg class="blog-curves" style="top:690px" viewBox="0 0 1200 150" preserveAspectRatio="none"><path d="M0 150H1200V110Q600 -20 0 110Z" fill="#fff"/></svg>
  <h2 class="section-title">LATEST BLOG</h2>
  <svg class="title-arc" style="top:228px" viewBox="0 0 60 14"><path d="M4 3 Q30 16 56 3" stroke="#fff" stroke-width="4" fill="none" stroke-linecap="round"/></svg>
  <div class="blog-cards">
    <article class="blog-card">
      <div class="blog-photo" role="img" aria-label="Photo of a smiling patient with a dentist" style="background:linear-gradient(150deg,#cfe7f1,#e8cdbd)"></div>
      <h3>NEMO ENIM IPSAM VOLUP</h3>
      <p>Simple tips to help you keep your teeth clean and bright between your regular checkups.</p>
      <div class="blog-date"><svg width="14" height="14"><rect x="1" y="2" width="12" height="11" fill="none" stroke="var(--blue)" stroke-width="1.5"/><path d="M1 5h12" stroke="var(--blue)" stroke-width="1.5"/></svg>March 25, 2019</div>
    </article>
    <article class="blog-card">
      <div class="blog-photo" role="img" aria-label="Photo of a dentist beside a treatment chair" style="background:linear-gradient(150deg,#dfe9ef,#7fa8c4)"></div>
      <h3>NEMO ENIM IPSAM VOLUP</h3>
      <p>What to expect during your first visit and how our team keeps every step relaxed.</p>
      <div class="blog-date"><svg width="14" height="14"><rect x="1" y="2" width="12" height="11" fill="none" stroke="var(--blue)" stroke-width="1.5"/><path d="M1 5h12" stroke="var(--blue)" stroke-width="1.5"/></svg>March 25, 2019</div>
    </article>
    <article class="blog-card">
      <div class="blog-photo" role="img" aria-label="Photo of a girl holding a tooth model" style="background:linear-gradient(150deg,#f0e0d6,#cfe3ee)"></div>
      <h3>NEMO ENIM IPSAM VOLUP</h3>
      <p>Helping kids build healthy brushing habits early makes every future visit much easier.</p>
      <div class="blog-date"><svg width="14" height="14"><rect x="1" y="2" width="12" height="11" fill="none" stroke="var(--blue)" stroke-width="1.5"/><path d="M1 5h12" stroke="var(--blue)" stroke-width="1.5"/></svg>March 25, 2019</div>
    </article>
  </div>
</section>

<h2 class="section-title" style="top:3486px">CASES &amp; REVIEWS</h2>
<svg class="title-arc" style="top:3546px" viewBox="0 0 60 14"><path d="M4 3 Q30 16 56 3" stroke="var(--blue)" stroke-width="4" fill="none" stroke-linecap="round"/></svg>

<span class="review-arrow" style="left:100px"><svg width="16" height="16"><path d="M11 2 5 8l6 6" stroke="#fff" stroke-width="2.5" fill="none"/></svg></span>
<span class="review-arrow" style="left:1054px"><svg width="16" height="16"><path d="M5 2l6 6-6 6" stroke="#fff" stroke-width="2.5" fill="none"/></svg></span>
<div class="review-brand"><span class="brand-square"></span>The Bright Arch Clinic</div>
<div class="quote-mark" style="left:530px;top:3596px">“</div>
<p class="review-text">The whole team made me feel at ease from the moment I walked in. My cleaning was gentle, the staff explained every step, and my new smile looks natural and bright. Booking online was quick and simple too.</p>
<div class="quote-mark" style="left:700px;top:3806px">”</div>
<p class="review-author">Daniel Reyes<br>The Bright Arch Clinic</p>

<footer class="site-footer">
  <div class="brand footer-brand"><span class="brand-square"></span>The Bright Arch Clinic</div>
  <div class="social"><span></span><span></span><span></span><span></span></div>
  <div class="footer-col" style="left:352px;width:290px">
    <h4>SIGN UP TO RECEIVE EMAIL</h4>
    <p>Get news, health tips and special offers from our team sent straight to your inbox.</p>
    <div class="email-field">Enter Email</div>
    <span class="btn subscribe">Subscribe</span>
  </div>
  <div class="footer-col" style="left:672px;width:230px">
    <h4>CONTACT US</h4>
    <div class="contact-line"><svg width="14" height="18"><path d="M7 1a6 6 0 0 1 6 6c0 4-6 10-6 10S1 11 1 7a6 6 0 0 1 6-6z" fill="#ddd"/><circle cx="7" cy="7" r="2" fill="#111"/></svg><span>48 Harbor Lane<br>Suite 12<br>Brookline, MA 02446</span></div>
    <div class="contact-line"><svg width="16" height="16"><path d="M3 1l3 3-2 2c1 3 3 5 6 6l2-2 3 3-2 2C7 15 1 9 1 3z" fill="#ddd"/></svg><span>Phone :<br>1-617-555-0142</span></div>
    <div class="contact-line"><svg width="16" height="12"><rect x="1" y="1" width="14" height="10" fill="none" stroke="#ddd" stroke-width="1.5"/><path d="M1 1l7 6 7-6" stroke="#ddd" stroke-width="1.5" fill="none"/></svg><span>Email :<br>info@thebrightarchclinic.com</span></div>
  </div>
  <div class="footer-col" style="left:928px;width:160px">
    <h4>QUICK LINKS</h4>
    <ul class="quick-links"><li>Home</li><li>Meet Us</li><li>Services</li><li>Patient Info</li><li>Cases &amp; Reviews</li><li>Blog</li><li>Contact</li></ul>
  </div>
</footer>
<div class="copyright">Copyright © The Bright Arch Clinic 2019. All rights reserved. | Policy | Returns</div>

</body>
</html>
```